Concise,Good colour matching,Good looks design for "HERD SCAN QUICK ASSAY FOR LIVESTOCK"

Product Positioning: Affordable test for Large Animals (Livestock/Veterinary Use)
Product Name: HERD SCAN Quick Assay Kit (for large animals, e.g., cattle, horses, swine,Avian,sheep).

2. Packaging Requirements

A. Visual Design
Color Scheme:
Green/Blue/Orange/Yellow/Red/Gray/White(chose 2~4 colors)

Mandatory Info:
Brand logo ("HERD SCAN")

Target Market(s)

Southeast Asia, Africa, Middle East, South America

Industry/Entity Type

Veterinary diagnostic for LIVESTOCK

Colors

Designer to choose colors to be used in the design.

Requirements
Nice to have
• Concise,Good colour matching,Good looks

```html
<!DOCTYPE html>
<html lang="en">
<head>
<meta charset="utf-8">
<title>HERD SCAN Quick Assay Kit – Carton Dieline</title>
<link href="https://fonts.googleapis.com/css2?family=Montserrat:wght@500;600;700;800&family=Open+Sans:wght@400&display=swap" rel="stylesheet">
<style>
  :root{
    --brand-blue:#00318a;
    --brand-green:#1fb41f;
    --photo-dark:#0f3a10;
    --photo-mid:#2f8a2b;
    --photo-light:#8fd08a;
    --white:#ffffff;
    --line:#1a1a1a;
  }
  *{box-sizing:border-box;margin:0;padding:0}
  html,body{width:1200px;height:828px;overflow:hidden;background:var(--white)}
  .canvas{position:relative;width:1200px;height:828px;font-family:"Montserrat",sans-serif}
  .dieline{position:absolute;left:0;top:0}
  .panel{position:absolute;overflow:hidden}
  .blue{background:var(--brand-blue);color:var(--white)}
  .rot{position:absolute;display:flex}

  /* dimension labels */
  .dim-label{position:absolute;font-family:"Open Sans",sans-serif;font-size:20px;color:#111}
  .dim-vertical{transform:rotate(90deg);transform-origin:left top}

  /* brand name */
  .brand{font-weight:800;letter-spacing:0.5px;line-height:1;white-space:nowrap}
  .brand-green{color:var(--brand-green)}
  .brand-white{color:var(--white)}
  .brand-blue{color:var(--brand-blue)}
  .mark{border:2px solid var(--brand-green);position:absolute}

  .tagline{font-weight:700;color:var(--white);line-height:1.1;white-space:nowrap}
  .small-info{font-weight:600;font-size:7.4px;line-height:1.35;color:var(--white);white-space:nowrap}

  /* photo grid */
  .photo-grid{position:absolute;left:230px;top:282px;width:212px;height:227px;display:grid;grid-template-columns:repeat(3,1fr);grid-template-rows:repeat(2,1fr)}
  .photo{background:linear-gradient(150deg,var(--photo-light),var(--photo-mid) 45%,var(--photo-dark))}
  .photo:nth-child(2){background:linear-gradient(180deg,var(--photo-mid),var(--photo-dark))}
  .photo:nth-child(3){background:linear-gradient(200deg,var(--photo-light),var(--photo-mid))}
  .photo:nth-child(4){background:linear-gradient(160deg,var(--photo-mid),var(--photo-light))}
  .photo:nth-child(5){background:linear-gradient(120deg,var(--photo-dark),var(--photo-light))}
  .photo:nth-child(6){background:linear-gradient(20deg,var(--photo-dark),var(--photo-light))}

  .benefits{font-size:6.4px;line-height:1.35;color:var(--white);font-weight:500}
  .benefits b{color:var(--white);font-weight:700}
</style>
</head>
<body>
<div class="canvas">

  <!-- dieline outline & flaps -->
  <svg class="dieline" width="1200" height="828" viewBox="0 0 1200 828" fill="none" stroke="#1a1a1a" stroke-width="1.2">
    <!-- top tuck tab -->
    <path d="M608 118 V100 Q608 92 616 92 H910 Q918 92 918 100 V118" fill="#fff"/>
    <!-- bottom tuck tab -->
    <path d="M608 675 V692 Q608 700 616 700 H910 Q918 700 918 692 V675" fill="#fff"/>
    <!-- dust flaps -->
    <polygon points="443,282 443,260 464,153 601,153 607,282" fill="#fff"/>
    <polygon points="918,282 923,153 1060,153 1082,260 1082,282" fill="#fff"/>
    <polygon points="443,509 443,531 464,638 601,638 607,509" fill="#fff"/>
    <polygon points="918,509 923,638 1060,638 1082,531 1082,509" fill="#fff"/>
    <!-- glue flap -->
    <polygon points="134,283 104,294 104,499 134,509" fill="#fff"/>
    <!-- main body outline -->
    <rect x="134" y="282" width="948" height="227"/>
    <rect x="608" y="118" width="310" height="557"/>
    <!-- dimension arrows -->
    <g stroke="#111" stroke-width="1" fill="#111">
      <line x1="146" y1="224" x2="440" y2="224"/>
      <polygon points="144,224 150,221 150,227" stroke="none"/>
      <polygon points="442,224 436,221 436,227" stroke="none"/>
      <line x1="1098" y1="285" x2="1098" y2="506"/>
      <polygon points="1098,283 1095,289 1101,289" stroke="none"/>
      <polygon points="1098,508 1095,502 1101,502" stroke="none"/>
      <line x1="1098" y1="512" x2="1098" y2="671"/>
      <polygon points="1098,510 1095,516 1101,516" stroke="none"/>
      <polygon points="1098,673 1095,667 1101,667" stroke="none"/>
    </g>
  </svg>

  <div class="dim-label" style="left:241px;top:188px">150mm</div>
  <div class="dim-label dim-vertical" style="left:1126px;top:358px">110mm</div>
  <div class="dim-label dim-vertical" style="left:1126px;top:545px">80mm</div>

  <!-- end flap: white panel -->
  <section class="panel end-white" style="left:134px;top:282px;width:46px;height:227px;background:var(--white)">
    <div class="rot" style="left:-90px;top:90px;width:227px;height:46px;transform:rotate(90deg);align-items:center;justify-content:flex-end;padding-right:12px">
      <span class="brand brand-blue" style="font-size:19px">HERD SCAN</span>
    </div>
  </section>

  <!-- tagline strip -->
  <section class="panel blue tag-strip" style="left:180px;top:282px;width:50px;height:227px">
    <div class="rot" style="left:-88px;top:88px;width:227px;height:50px;transform:rotate(90deg);flex-direction:column;justify-content:center;padding-left:10px">
      <span class="tagline" style="font-size:10.5px">Affordable Diagnostics<br>for Healthy Herds</span>
    </div>
    <div class="mark" style="left:13px;top:170px;width:24px;height:24px"></div>
  </section>

  <!-- livestock photo area -->
  <div class="photo-grid">
    <div class="photo" role="img" aria-label="Photo of a rooster, green duotone"></div>
    <div class="photo" role="img" aria-label="Photo of a herd of cattle in pasture, green duotone"></div>
    <div class="photo" role="img" aria-label="Photo of a horse in a field, green duotone"></div>
    <div class="photo" role="img" aria-label="Photo of a sheep, green duotone"></div>
    <div class="photo" role="img" aria-label="Photo of a pig, green duotone"></div>
    <div class="photo" role="img" aria-label="Photo of a cow, green duotone"></div>
  </div>

  <!-- left side panel -->
  <section class="panel blue side-left" style="left:442px;top:282px;width:166px;height:227px">
    <div class="rot" style="left:-30.5px;top:30.5px;width:227px;height:166px;transform:rotate(-90deg);flex-direction:column;align-items:center;padding-top:16px">
      <span class="brand brand-white" style="font-size:24px">HERD SCAN</span>
      <p class="small-info" style="margin-top:12px;text-align:center">Manufactured by FIELDVET LABS<br>Storage: 2-30 °C, Do not freeze<br>See the instructions for other contents</p>
    </div>
  </section>

  <!-- front panel -->
  <section class="panel blue front" style="left:608px;top:282px;width:310px;height:227px">
    <div class="mark" style="left:29px;top:22px;width:184px;height:184px"></div>
    <div style="position:absolute;left:141px;top:98px">
      <span class="brand brand-white" style="font-size:18px">HERD SCAN</span>
      <p class="tagline" style="font-size:11.5px;margin-top:4px">Affordable Diagnostics<br>for Healthy Herds</p>
    </div>
  </section>

  <!-- right side panel -->
  <section class="panel blue side-right" style="left:918px;top:282px;width:164px;height:227px">
    <div class="rot" style="left:-31.5px;top:31.5px;width:227px;height:164px;transform:rotate(90deg);flex-direction:column;align-items:center;padding-top:14px">
      <span class="brand brand-white" style="font-size:24px">HERD SCAN</span>
      <p class="small-info" style="margin-top:12px;text-align:center">Manufactured by FIELDVET LABS<br>Storage: 2-30 °C, Do not freeze<br>See the instructions for other contents</p>
    </div>
  </section>

  <!-- top panel -->
  <section class="panel blue top-panel" style="left:608px;top:118px;width:310px;height:164px">
    <span class="brand brand-white" style="position:absolute;right:10px;top:12px;font-size:25px">HERD SCAN</span>
    <div class="mark" style="left:206px;top:46px;width:92px;height:92px"></div>
    <p class="tagline" style="position:absolute;left:22px;top:104px;font-size:14.5px">Affordable Diagnostics<br>for Healthy Herds</p>
  </section>

  <!-- bottom panel (printed inverted) -->
  <section class="panel blue bottom-panel" style="left:608px;top:509px;width:310px;height:166px">
    <div style="position:absolute;inset:0;transform:rotate(180deg)">
      <div style="position:absolute;left:10px;top:16px;display:flex;width:290px;justify-content:space-between;align-items:center">
        <span class="brand brand-green" style="font-size:13px">QUICK ASSAY</span>
        <span class="brand brand-white" style="font-size:21px">HERD SCAN</span>
      </div>
      <div class="benefits" style="position:absolute;left:14px;top:58px;width:170px">
        <p><b>Fast &amp; Efficient:</b> Rapid test results in less than 10 minutes from prep to completion</p>
        <p style="margin-top:3px"><b>Affordable:</b> Colloidal gold-based rapid tests that combine high accuracy with cost-effectiveness.</p>
        <p style="margin-top:3px"><b>Reliable &amp; Simple:</b> Stable test performance with 2-30 °C, Easy to operate, no professional skills required.</p>
      </div>
      <div class="mark" style="left:210px;top:52px;width:80px;height:80px"></div>
    </div>
  </section>

</div>
</body>
</html>
```